Marlowe Group needs a business card

I would like the card to be simple but modern and elegant.
I like black and white.
or black and gold.
we are a private finance lender and also are involved in property and property developments.

please look at the business card photos i provided i would like M.G only one one side and all the other details on the other side use fonts that tie in with my theme.

Industry/Entity Type

Finance

Contact Information for Business Card

Marlowe Group (M.G) Daniel Marlowe M: 0413586207 E: danmarl@inboxmail.test

Font styles to use
Other font styles liked:
• Use fonts that would reflect our business

Colors
000000
ffffff

Requirements
Must have
• one side of details
• other side has either M.G or Marlowe Group like in the photos provided

```html
<!DOCTYPE html>
<html lang="en">
<head>
<meta charset="utf-8">
<title>Marlowe Group – Business Card</title>
<link rel="stylesheet" href="https://fonts.googleapis.com/css2?family=Montserrat:wght@400;600;800&display=swap">
<style>
  :root {
    --backdrop: #7f8383;
    --card: #f1f1f1;
    --ink: #000000;
    --ink-soft: #1c1c1c;
    --shadow: rgba(0, 0, 0, 0.28);
  }
  * { margin: 0; padding: 0; box-sizing: border-box; }
  html, body {
    width: 1200px;
    height: 814px;
    overflow: hidden;
    background: var(--backdrop);
  }
  .canvas {
    position: relative;
    width: 1200px;
    height: 814px;
    display: flex;
    align-items: center;
    justify-content: center;
    gap: 44px;
  }
  .card {
    position: relative;
    width: 500px;
    height: 306px;
    background: var(--card);
    box-shadow: 0 18px 40px var(--shadow);
    color: var(--ink);
  }

  /* Details side */
  .card-details .initials {
    position: absolute;
    top: 40px;
    right: 40px;
    font-family: "Montserrat", Arial, sans-serif;
    font-weight: 600;
    font-size: 46px;
    letter-spacing: 1px;
    line-height: 1;
    color: var(--ink);
  }
  .card-details .contact {
    position: absolute;
    left: 40px;
    top: 112px;
    font-family: "Montserrat", Arial, sans-serif;
    color: var(--ink-soft);
  }
  .contact .name {
    font-weight: 600;
    font-size: 24px;
    letter-spacing: 0.3px;
    margin-bottom: 10px;
    color: var(--ink);
  }
  .contact .line {
    font-weight: 400;
    font-size: 16px;
    line-height: 1.45;
    letter-spacing: 0.3px;
  }

  /* Brand side */
  .card-brand {
    display: flex;
    align-items: center;
    justify-content: center;
  }
  .card-brand .company-name {
    font-family: "Montserrat", Arial, sans-serif;
    font-weight: 800;
    font-size: 34px;
    letter-spacing: 3px;
    text-transform: uppercase;
    color: var(--ink);
  }
</style>
</head>
<body>
  <main class="canvas">
    <section class="card card-details" aria-label="Business card, contact side">
      <p class="initials">M.G</p>
      <div class="contact">
        <p class="name">Daniel Marlowe</p>
        <p class="line">0413586207</p>
        <p class="line">danmarl@inboxmail.test</p>
        <p class="line">www.marlowegroup.test</p>
      </div>
    </section>

    <section class="card card-brand" aria-label="Business card, brand side">
      <p class="company-name">Marlowe Group</p>
    </section>
  </main>
</body>
</html>
```